Garlic Farm for Farm Sales/Restaurant sales

Need a professional, but appealing to agriculture world. We are selling 27 kinds of Organic Garlic from a farm in Simla,CO. I have uploaded logo and business information-we are going to need a template, because I will need to use it for four separate people.
-We are trying to appeal to Farm to table restaurants
-As well as growers/farmers

Target Market(s)

Agriculture Sales/Restaurants-Organic

Industry/Entity Type

Agriculture

Contact Information for Business Card

Want it to look more unique then your average kelto stock card- I want it to look amazing

Font styles to use
Sans Serif

Colors
0455a3
ec1f27
fbed22
ffffff

Requirements
Must have
• Just be creative
Nice to have
• Colorful
Should not have
• plain

```html
<!DOCTYPE html>
<html lang="en">
<head>
<meta charset="utf-8">
<title>Ridgeline Garlic – Business Card</title>
<link rel="stylesheet" href="https://fonts.googleapis.com/css2?family=Josefin+Sans:wght@400;600&display=swap">
<style>
  :root {
    --stage: #2e2e30;
    --navy: #1b2f5e;
    --red: #d8232c;
    --yellow: #f2e12a;
    --white: #ffffff;
    --ink: #1b2f5e;
  }
  * { box-sizing: border-box; margin: 0; padding: 0; }
  html, body {
    width: 1200px; height: 900px; overflow: hidden;
    background: var(--stage);
    font-family: "Josefin Sans", Arial, sans-serif;
  }
  .stage { position: relative; width: 1200px; height: 900px; }
  .card {
    position: absolute; width: 700px; height: 400px;
    box-shadow: 0 10px 30px rgba(0,0,0,.45);
  }
  .card-back { left: 110px; top: 40px; background: var(--navy); }
  .card-front { left: 390px; top: 460px; background: var(--white); }

  .brand {
    position: absolute; left: 0; right: 0; top: 135px;
    display: flex; align-items: center; justify-content: center; gap: 14px;
  }
  .brand-dot { width: 38px; height: 38px; border-radius: 50%; background: var(--red); }
  .brand-name { color: var(--white); font-weight: 600; font-size: 44px; letter-spacing: 1px; }
  .social {
    position: absolute; left: 0; right: 0; top: 235px;
    display: flex; justify-content: center; gap: 16px;
  }
  .social-dot { width: 26px; height: 26px; border-radius: 50%; background: var(--white); }

  .front-brand {
    position: absolute; left: 40px; top: 150px; width: 250px;
    display: flex; align-items: center; gap: 10px;
  }
  .front-brand .brand-dot { width: 30px; height: 30px; flex: none; }
  .front-brand .brand-name { color: var(--red); font-size: 30px; }
  .divider {
    position: absolute; left: 310px; top: 110px; width: 2px; height: 140px;
    background: var(--yellow);
  }
  .contact { position: absolute; left: 345px; top: 120px; color: var(--ink); }
  .person { font-size: 34px; font-weight: 600; letter-spacing: 1px; margin-bottom: 14px; }
  .person .surname { color: var(--red); }
  .contact-line {
    display: flex; align-items: center; gap: 10px;
    font-size: 17px; margin-bottom: 8px;
  }
  .contact-line .hl { color: var(--red); }
  .icon { width: 16px; height: 16px; flex: none; }
  .address {
    position: absolute; left: 345px; top: 320px;
    color: var(--ink); font-size: 18px;
  }
</style>
</head>
<body>
<div class="stage">
  <section class="card card-back">
    <div class="brand">
      <span class="brand-dot"></span>
      <span class="brand-name">Ridgeline Garlic</span>
    </div>
    <div class="social">
      <span class="social-dot"></span>
      <span class="social-dot"></span>
      <span class="social-dot"></span>
      <span class="social-dot"></span>
    </div>
  </section>

  <section class="card card-front">
    <div class="front-brand">
      <span class="brand-dot"></span>
      <span class="brand-name">Ridgeline Garlic</span>
    </div>
    <div class="divider"></div>
    <div class="contact">
      <div class="person">DANA <span class="surname">WELLS</span></div>
      <div class="contact-line">
        <svg class="icon" viewBox="0 0 16 16"><rect width="16" height="16" rx="3" fill="#d8232c"/><path d="M5 4l2 2-1 1c.6 1.3 1.7 2.4 3 3l1-1 2 2-1.5 1.5C7.5 12 4 8.5 3.5 5.5z" fill="#fff"/></svg>
        <span>555-014-2290</span>
      </div>
      <div class="contact-line">
        <svg class="icon" viewBox="0 0 16 16"><rect width="16" height="16" rx="3" fill="#d8232c"/><rect x="3.5" y="5" width="9" height="6.5" fill="none" stroke="#fff" stroke-width="1.2"/><path d="M3.5 5l4.5 3.5L12.5 5" fill="none" stroke="#fff" stroke-width="1.2"/></svg>
        <span>Dana@RLGarlic.com</span>
      </div>
      <div class="contact-line">
        <svg class="icon" viewBox="0 0 16 16"><rect width="16" height="16" rx="3" fill="#d8232c"/><circle cx="8" cy="8" r="4.5" fill="none" stroke="#fff" stroke-width="1.1"/><ellipse cx="8" cy="8" rx="2" ry="4.5" fill="none" stroke="#fff" stroke-width="1"/><path d="M3.5 8h9" stroke="#fff" stroke-width="1"/></svg>
        <span>www.<span class="hl">RLG</span>arlic.com</span>
      </div>
    </div>
    <div class="address">P.O. Box 72 Elbert, CO 80106</div>
  </section>
</div>
</body>
</html>
```